Marlowe Group needs a business card

I would like the card to be simple but modern and elegant.
I like black and white.
or black and gold.
we are a private finance lender and also are involved in property and property developments.

please look at the business card photos i provided i would like M.G only one one side and all the other details on the other side use fonts that tie in with my theme.

Industry/Entity Type

Finance

Contact Information for Business Card

Marlowe Group (M.G) Daniel Marlowe M: 0413586207 E: danmarl@inboxmail.test

Font styles to use
Other font styles liked:
• Use fonts that would reflect our business

Colors
000000
ffffff

Requirements
Must have
• one side of details
• other side has either M.G or Marlowe Group like in the photos provided

```html
<!DOCTYPE html>
<html lang="en">
<head>
<meta charset="utf-8">
<title>Marlowe Group — Business Card</title>
<link rel="stylesheet" href="https://fonts.googleapis.com/css2?family=Sorts+Mill+Goudy&display=swap">
<style>
  :root {
    --page: #ffffff;
    --card: #000000;
    --gold: #857049;
    --serif: "Sorts Mill Goudy", "Goudy Old Style", Georgia, serif;
  }
  * { margin: 0; padding: 0; box-sizing: border-box; }
  html, body {
    width: 960px;
    height: 1200px;
    overflow: hidden;
    background: var(--page);
  }
  .sheet {
    position: relative;
    width: 960px;
    height: 1200px;
  }
  .card {
    position: absolute;
    left: 60px;
    width: 840px;
    height: 480px;
    background: var(--card);
    color: var(--gold);
    font-family: var(--serif);
  }
  .card--front { top: 86px; }
  .card--back  { top: 634px; }

  .frame-outer {
    position: absolute;
    inset: 14px;
    border: 3px solid var(--gold);
  }
  .frame-inner {
    position: absolute;
    inset: 20px;
    border: 1.5px solid var(--gold);
  }

  /* Front */
  .panel {
    position: absolute;
    left: 101px;
    top: 72px;
    width: 638px;
    height: 336px;
    border: 1.5px solid var(--gold);
  }
  .rule-pair {
    position: absolute;
    top: 235px;
    width: 113px;
    height: 9px;
    border-top: 1.5px solid var(--gold);
    border-bottom: 1.5px solid var(--gold);
  }
  .rule-pair--left  { left: 101px; }
  .rule-pair--right { left: 626px; }
  .company-name {
    position: absolute;
    left: 0;
    right: 0;
    top: 218px;
    text-align: center;
    font-size: 39px;
    line-height: 40px;
    letter-spacing: 0.5px;
    text-transform: uppercase;
  }

  /* Back */
  .monogram {
    position: absolute;
    left: 0;
    right: 0;
    top: 84px;
    text-align: center;
    font-size: 44px;
    line-height: 52px;
  }
  .person-name {
    position: absolute;
    left: 0;
    right: 0;
    top: 193px;
    text-align: center;
    font-size: 45px;
    line-height: 48px;
  }
  .name-rule {
    position: absolute;
    left: 258px;
    top: 246px;
    width: 323px;
    height: 3px;
    background: var(--gold);
  }
  .contact {
    position: absolute;
    left: 0;
    right: 0;
    text-align: center;
    font-size: 37px;
    line-height: 40px;
  }
  .contact--phone { top: 282px; }
  .contact--email { top: 353px; font-size: 35px; }
</style>
</head>
<body>
<main class="sheet">
  <section class="card card--front" aria-label="Card front">
    <div class="frame-outer"></div>
    <div class="frame-inner"></div>
    <div class="panel"></div>
    <div class="rule-pair rule-pair--left"></div>
    <div class="rule-pair rule-pair--right"></div>
    <h1 class="company-name">Marlowe Group</h1>
  </section>

  <section class="card card--back" aria-label="Card back">
    <div class="frame-outer"></div>
    <div class="frame-inner"></div>
    <p class="monogram">M.G</p>
    <h2 class="person-name">Daniel Marlowe</h2>
    <div class="name-rule"></div>
    <p class="contact contact--phone">M: 0413586207</p>
    <p class="contact contact--email">E: danmarl@inboxmail.test</p>
  </section>
</main>
</body>
</html>
```